Brightfen Business Card Redesign & Logo Update

We need to update our business cards to something more modern and fresh. Brightfen can provide the current color schemes and old design examples, but welcome creativity in helping us with this redesign. PLEASE NOTE that we no longer utilize the "tree" and/or "leaf" imagery in our branding. If able would apprecaite an update on the quality of our "words only" logo in Ai. / PNG formats too.

Target Market(s)

Investors, landowners, corporate partners, contractors

Industry/Entity Type

Environmental Restoration & Conservation

Contact Information for Business Card

Logo, persons name, title, mailing address, phone and email, website url

Font styles to use
Other font styles liked:
• Merriweather

Requirements
Nice to have
• Logo, persons name, title, mailing address, phone and email, website url, but open to ideams
Should not have
• No all back backgrounds

```html
<!DOCTYPE html>
<html lang="en">
<head>
<meta charset="UTF-8">
<title>Brightfen Business Card</title>
<link href="https://fonts.googleapis.com/css2?family=Lato:wght@400;700;900&display=swap" rel="stylesheet">
<style>
  :root {
    --backdrop: #8f8f8f;
    --paper: #ffffff;
    --brand-green: #147a36;
    --brand-green-dark: #0f6a2c;
    --brand-orange: #ec7a06;
    --ink: #111111;
  }
  * { margin: 0; padding: 0; box-sizing: border-box; }
  html, body {
    width: 1200px;
    height: 1200px;
    overflow: hidden;
    background: var(--backdrop);
    font-family: "Lato", Arial, sans-serif;
  }
  .card {
    position: absolute;
    left: 281px;
    width: 642px;
    height: 367px;
    overflow: hidden;
  }
  .card--front { top: 195px; background: var(--paper); }
  .card--back { top: 639px; background: var(--brand-green); }

  .logo {
    position: absolute;
    left: 0;
    width: 100%;
    text-align: center;
  }
  .card--front .logo { top: 62px; left: -6px; }
  .logo__name {
    display: block;
    font-weight: 900;
    letter-spacing: 2px;
    line-height: 1;
  }
  .card--front .logo__name { font-size: 62px; color: var(--brand-green); }
  .logo__tagline {
    display: block;
    font-weight: 700;
    text-transform: uppercase;
    line-height: 1;
  }
  .card--front .logo__tagline { font-size: 19px; color: var(--ink); margin-top: 10px; letter-spacing: 0.5px; }

  .card--back .logo { top: 110px; }
  .card--back .logo__name { font-size: 92px; color: var(--paper); letter-spacing: 3px; }
  .card--back .logo__tagline { font-size: 28px; color: var(--paper); margin-top: 14px; letter-spacing: 0.5px; }

  .band {
    position: absolute;
    top: 216px;
    height: 151px;
    color: var(--paper);
  }
  .band--person { left: 0; width: 322px; background: var(--brand-green); }
  .band--contact { left: 326px; width: 316px; background: var(--brand-orange); }

  .person__name {
    position: absolute;
    left: 40px;
    top: 29px;
    font-size: 26px;
    font-weight: 700;
    letter-spacing: 0.3px;
  }
  .person__title {
    position: absolute;
    left: 40px;
    top: 60px;
    font-size: 18.5px;
  }
  .person__address {
    position: absolute;
    left: 41px;
    top: 86px;
    font-size: 15.5px;
    line-height: 19px;
  }

  .contact-list {
    position: absolute;
    right: 40px;
    top: 29px;
    list-style: none;
    text-align: right;
    font-size: 15.5px;
  }
  .contact-list li {
    display: flex;
    justify-content: flex-end;
    align-items: center;
    height: 22.5px;
  }
  .contact-list svg {
    width: 12px;
    height: 12px;
    margin-left: 11px;
    flex: none;
  }
</style>
</head>
<body>

  <section class="card card--front">
    <div class="logo">
      <span class="logo__name">BRIGHTFEN</span>
      <span class="logo__tagline">Environmental Credit Company</span>
    </div>

    <div class="band band--person">
      <h1 class="person__name">DANIEL HARPER</h1>
      <p class="person__title">Founder &amp; CEO</p>
      <p class="person__address">123 Anywhere St<br>Any City, State 12345</p>
    </div>

    <div class="band band--contact">
      <ul class="contact-list">
        <li>(123) 456-7890
          <svg viewBox="0 0 12 12" aria-hidden="true"><path d="M2.5 1 L4.5 1 L5.2 3.6 L4 4.6 C4.6 6 5.8 7.2 7.3 7.9 L8.3 6.8 L11 7.4 L11 9.5 C11 10.3 10.3 11 9.5 11 C5 10.7 1.3 7 1 2.5 C1 1.7 1.7 1 2.5 1 Z" fill="#fff"/></svg>
        </li>
        <li>(123) 456-7890
          <svg viewBox="0 0 12 12" aria-hidden="true"><rect x="3" y="0.8" width="6.5" height="10.4" rx="1" fill="none" stroke="#fff" stroke-width="1.4"/><circle cx="6.25" cy="9.3" r="0.7" fill="#fff"/></svg>
        </li>
        <li>hello@yourwebsite.com
          <svg viewBox="0 0 12 12" aria-hidden="true"><rect x="0.5" y="2.5" width="11" height="7.5" fill="#fff"/><path d="M0.8 2.8 L6 7 L11.2 2.8" fill="none" stroke="#ec7a06" stroke-width="1"/></svg>
        </li>
        <li>www.yourwebsite.com
          <svg viewBox="0 0 12 12" aria-hidden="true"><circle cx="6" cy="6" r="5.2" fill="none" stroke="#fff" stroke-width="1.4"/><path d="M3.5 3 C5 3.5 5 5 6.5 5.5 C7.5 6 6.5 8 5.5 9.5 M7.5 1.5 C8 3 9.5 3 10.5 4" fill="none" stroke="#fff" stroke-width="1.3"/></svg>
        </li>
      </ul>
    </div>
  </section>

  <section class="card card--back">
    <div class="logo">
      <span class="logo__name">BRIGHTFEN</span>
      <span class="logo__tagline">Environmental Credit Company</span>
    </div>
  </section>

</body>
</html>
```